Climbing Gear Company Stationary Design

We need some new stationary to standardise our business.
We require:

Business Card
A4 Letterhead
With complements slip

Our business is a Distributor and retailer of rock climbing equipment throughout Australia.
We need to the stationary (business card in particular) to reflect this.

Target Market(s)

customers, other retail outlets, overseas manufacturers.

Industry/Entity Type

Business

Requirements
Must have
• company logo
website url- www.ridgetopgearworks.com.au
email - mark@ridgetopgearworks.com
Business Address: Unit 3, 14-16 Marlowe Street, Kestrel Bay, VIC, 2371
Phone: 0438 627 194
my Name (on Business card) - Gordon Pellimore
use of Blue colour in our logo

```html
<!DOCTYPE html>
<html lang="en">
<head>
<meta charset="utf-8">
<title>Ridgetop Gearworks – Business Card</title>
<link rel="stylesheet" href="https://fonts.googleapis.com/css2?family=Open+Sans:wght@400;600;700;800&display=swap">
<style>
  :root {
    --bg: #ece4d4;
    --card: #ffffff;
    --brand-blue: #23408e;
    --band-top: #3656a4;
    --band-bottom: #1f3a84;
    --accent-grey: #8a8a8a;
    --text-grey: #4a4a4a;
    --shadow: rgba(60, 40, 10, 0.35);
  }
  * { box-sizing: border-box; margin: 0; padding: 0; }
  html, body {
    width: 1200px; height: 483px; overflow: hidden;
    background: var(--bg);
    font-family: "Open Sans", Arial, sans-serif;
  }
  .canvas { position: relative; width: 1200px; height: 483px; }
  .card {
    position: absolute; top: 90px; width: 525px; height: 300px;
    background: var(--card);
    box-shadow: 3px 4px 8px var(--shadow);
  }
  .card--front { left: 60px; }
  .card--back { left: 609px; }
  .brand {
    position: absolute; left: 0; right: 0; text-align: center;
  }
  .card--front .brand { top: 68px; }
  .card--back .brand { top: 95px; }
  .brand__name {
    color: var(--brand-blue);
    font-weight: 800;
    font-size: 33px;
    line-height: 1;
    letter-spacing: 0.3px;
  }
  .card--back .brand__name { font-size: 27px; }
  .brand__tagline {
    margin-top: 9px;
    color: var(--brand-blue);
    font-weight: 600;
    font-size: 13px;
    letter-spacing: 3.4px;
  }
  .card--back .brand__tagline { font-size: 11px; letter-spacing: 2.8px; margin-top: 8px; }
  .band {
    position: absolute; top: 204px; left: 0; width: 485px; height: 31px;
    background: linear-gradient(to bottom, var(--band-top) 0%, var(--band-top) 40%, var(--band-bottom) 55%, var(--band-bottom) 100%);
    color: #fff;
    display: flex; align-items: center; justify-content: center;
  }
  .band__name { font-weight: 700; font-size: 14px; letter-spacing: 0.4px; text-transform: uppercase; }
  .band__web { font-weight: 400; font-size: 13px; }
  .band-square {
    position: absolute; top: 204px; left: 488px; width: 37px; height: 31px;
    background: var(--accent-grey);
  }
  .contact {
    position: absolute; top: 248px; left: 0; right: 0; text-align: center;
    color: var(--text-grey); font-size: 10.5px; line-height: 19px;
  }
  .contact__item { margin: 0 6px; }
  .contact__site { color: var(--brand-blue); }
</style>
</head>
<body>
<main class="canvas">
  <section class="card card--front">
    <div class="brand">
      <div class="brand__name">RIDGETOP GEARWORKS</div>
      <div class="brand__tagline">THE ROPE•THE CRAG•THE JOURNEY</div>
    </div>
    <div class="band"><span class="band__name">Gordon Pellimore</span></div>
    <div class="band-square"></div>
    <div class="contact">
      <p>Unit 3, 14-16 Marlowe Street Kestrel Bay, VIC, 2371</p>
      <p>
        <span class="contact__item">P : 0438 627 194</span>
        <span class="contact__item">E : mark@ridgetopgearworks.com</span>
        <span class="contact__item">W: www.<span class="contact__site">ridgetopgearworks</span>.com.</span>
      </p>
    </div>
  </section>

  <section class="card card--back">
    <div class="brand">
      <div class="brand__name">RIDGETOP GEARWORKS</div>
      <div class="brand__tagline">THE ROPE•THE CRAG•THE JOURNEY</div>
    </div>
    <div class="band"><span class="band__web">www.ridgetopgearworks.com.</span></div>
    <div class="band-square"></div>
  </section>
</main>
</body>
</html>
```